Cover für ein Taschenbuch zum Thema Ruhestand gesucht!
Zielgruppe
Unsere Zielgruppe sind Senioren, bzw. Menschen im Alter 50+. Es handelt sich bei dem Buch um einen Ratgeber zum Thema 'Ruhestand'. Allerdings wird das Buch ebenso von einer jüngeren Zielgruppe gekauft, da der Ratgeber auch gerne an Eltern oder Großeltern verschenkt wird.
Aufgabenstellung
siehe Dateiupload
Format: 5,25' x 8'

```html
<!DOCTYPE html>
<html lang="de">
<head>
<meta charset="utf-8">
<title>Neue Freiheit – Buchcover</title>
<link rel="stylesheet" href="https://fonts.googleapis.com/css2?family=Cinzel:wght@400;700&family=Lora:wght@400&family=Playfair+Display:ital,wght@1,900&display=swap">
<style>
  :root {
    --page-bg: #f1efec;
    --sky-light: #fbeee0;
    --sky-peach: #f6cfae;
    --horizon: #f08a4b;
    --water: #e9a27e;
    --deck-rose: #c77e78;
    --deck-deep: #9a5a5e;
    --tagline: #7a2c1c;
    --band: rgba(255, 255, 255, 0.72);
    --ink: #1b1714;
  }
  * { margin: 0; padding: 0; box-sizing: border-box; }
  html, body {
    width: 1200px;
    height: 2296px;
    overflow: hidden;
    background: var(--page-bg);
  }
  .book-cover {
    position: absolute;
    left: 150px;
    top: 511px;
    width: 900px;
    height: 1273px;
    overflow: hidden;
    box-shadow: 0 18px 40px rgba(0, 0, 0, 0.18);
  }
  .cover-photo {
    position: absolute;
    inset: 0;
    background:
      linear-gradient(90deg, rgba(0,0,0,0.08) 0, rgba(255,255,255,0.15) 14px, rgba(0,0,0,0) 30px),
      linear-gradient(180deg,
        var(--sky-light) 0%,
        var(--sky-peach) 30%,
        var(--horizon) 40%,
        var(--water) 48%,
        var(--deck-rose) 70%,
        var(--deck-deep) 100%);
  }
  .tagline {
    position: absolute;
    left: 24px;
    top: 62px;
    width: 400px;
    text-align: center;
    font-family: "Lora", Georgia, serif;
    font-size: 34px;
    line-height: 50px;
    color: var(--tagline);
  }
  .title-band {
    position: absolute;
    left: 0;
    top: 982px;
    width: 773px;
    height: 188px;
    background: var(--band);
    clip-path: polygon(0 0, 92% 0, 100% 100%, 0 100%);
  }
  .book-title {
    position: absolute;
    left: 40px;
    top: 1002px;
    font-family: "Cinzel", "Times New Roman", serif;
    font-weight: 700;
    font-size: 72px;
    line-height: 1;
    letter-spacing: -1px;
    color: var(--ink);
    white-space: nowrap;
  }
  .book-subtitle {
    position: absolute;
    left: 42px;
    top: 1096px;
    font-family: "Cinzel", "Times New Roman", serif;
    font-weight: 400;
    font-size: 25px;
    line-height: 1;
    color: var(--ink);
    white-space: nowrap;
  }
  .author {
    position: absolute;
    left: 0;
    width: 948px;
    top: 1184px;
    text-align: center;
    font-family: "Playfair Display", Georgia, serif;
    font-style: italic;
    font-weight: 900;
    font-size: 38px;
    line-height: 1.2;
    color: var(--ink);
  }
</style>
</head>
<body>
  <main class="book-cover">
    <div class="cover-photo" role="img" aria-label="Foto: älteres Paar sitzt bei Sonnenuntergang auf dem Deck eines Segelbootes"></div>
    <p class="tagline">Kluge Ideen<br>und Anregungen,<br>mit denen Sie Ihren<br>Lebensabend mit<br>Freude gestalten<br>können</p>
    <div class="title-band"></div>
    <h1 class="book-title">NEUE FREIHEIT</h1>
    <p class="book-subtitle">Die schönste Zeit liegt noch vor Ihnen!</p>
    <p class="author">Lukas Brenner</p>
  </main>
</body>
</html>
```